Coastline Premier Retreats Business Card Design

Design a business card for Coastline Premier Retreats. Look at the website for colors and reference. Card should have logo, name, title, office number, mobile number, email, URL and a tagline like, "Luxury Hotel & Resort Email Marketing" (This might change).

https://www.coastlinepremierretreats.example

The rest I will leave up to your imagination.

Contact Information for Business Card

Logo, name, title, office number, mobile number, email, URL and a tagline like, "Luxury Hotel & Resort Email Marketing" (This might change).

```html
<!DOCTYPE html>
<html lang="en">
<head>
<meta charset="utf-8">
<title>Coastline Premier Retreats – Business Card</title>
<link rel="stylesheet" href="https://fonts.googleapis.com/css2?family=Open+Sans:wght@400;600;700&display=swap">
<style>
  :root {
    --backdrop: #232323;
    --card: #1f1f23;
    --orange: #f1731f;
    --white: #ffffff;
    --text-soft: #e9e9ea;
    --emboss: #29292e;
    --divider: #bdbdbd;
  }
  * { box-sizing: border-box; margin: 0; padding: 0; }
  html, body {
    width: 1200px; height: 780px; overflow: hidden;
    background: var(--backdrop);
    font-family: "Open Sans", Arial, sans-serif;
  }
  .canvas { position: relative; width: 1200px; height: 780px; }

  .card {
    position: absolute;
    width: 540px; height: 310px;
    background: var(--card);
    border-radius: 18px;
    overflow: hidden;
    box-shadow: 0 18px 40px rgba(0,0,0,.55);
  }
  .card--back { left: 70px; top: 70px; }
  .card--front { left: 590px; top: 400px; }

  .card__bands { position: absolute; left: 0; bottom: 0; width: 540px; height: 60px; }
  .band--orange { fill: var(--orange); }
  .band--white { fill: var(--white); }

  /* back side */
  .back-mark {
    position: absolute; left: 0; right: 0; top: 104px;
    display: flex; align-items: center; justify-content: center; gap: 14px;
  }
  .back-mark__square { width: 22px; height: 22px; background: var(--emboss); }
  .back-mark__name {
    font-weight: 700; font-size: 30px; letter-spacing: .5px;
    color: var(--emboss); text-transform: uppercase;
  }

  /* front side */
  .brand {
    position: absolute; left: 34px; top: 116px; width: 216px;
    display: flex; align-items: center; gap: 10px;
  }
  .brand__square { flex: none; width: 16px; height: 16px; background: var(--orange); }
  .brand__name {
    font-weight: 700; font-size: 19px; line-height: 1.2;
    color: var(--white); text-transform: uppercase;
  }

  .divider {
    position: absolute; left: 262px; top: 40px;
    width: 1px; height: 160px; background: var(--divider);
  }

  .person { position: absolute; left: 286px; top: 46px; }
  .person__name { font-size: 25px; font-weight: 700; color: var(--white); line-height: 1.1; }
  .person__first { color: var(--orange); }
  .person__title { font-size: 12.5px; font-weight: 600; color: var(--white); margin-top: 3px; }

  .contacts { list-style: none; margin-top: 14px; }
  .contacts__item {
    display: flex; align-items: center; gap: 9px;
    font-size: 11px; color: var(--text-soft); line-height: 1; margin-bottom: 7px;
  }
  .contacts__icon { width: 12px; height: 12px; flex: none; }
  .icon-stroke { fill: none; stroke: var(--orange); stroke-width: 1.6; }
  .icon-stroke--white { fill: none; stroke: var(--white); stroke-width: 1.4; }
  .icon-fill { fill: var(--orange); }

  .tagline {
    position: absolute; right: 40px; bottom: 64px;
    font-size: 14px; color: var(--orange);
  }
</style>
</head>
<body>
<main class="canvas">

  <section class="card card--back" aria-label="Card back">
    <div class="back-mark">
      <span class="back-mark__square"></span>
      <span class="back-mark__name">Coastline Premier Retreats</span>
    </div>
    <svg class="card__bands" viewBox="0 0 540 60" aria-hidden="true">
      <polygon class="band--white" points="232,34 540,6 540,40 250,42"/>
      <polygon class="band--orange" points="0,46 220,40 250,42 250,42 0,60"/>
      <polygon class="band--orange" points="0,44 224,40 240,44 0,60"/>
    </svg>
  </section>

  <section class="card card--front" aria-label="Card front">
    <div class="brand">
      <span class="brand__square"></span>
      <span class="brand__name">Coastline Premier Retreats</span>
    </div>

    <div class="divider"></div>

    <div class="person">
      <h1 class="person__name"><span class="person__first">Marisa</span> Kellner</h1>
      <p class="person__title">Managing Director</p>
      <ul class="contacts">
        <li class="contacts__item">
          <svg class="contacts__icon" viewBox="0 0 12 12" aria-hidden="true"><path class="icon-fill" d="M2.4 1l2 2.2-1 1.3c.7 1.5 1.8 2.6 3.3 3.3l1.3-1 2.2 2-1.2 1.6C5.4 10.3 1.7 6.6 1 2.2z"/></svg>
          (555) 214-0386
        </li>
        <li class="contacts__item">
          <svg class="contacts__icon" viewBox="0 0 12 12" aria-hidden="true"><rect class="icon-stroke--white" x="3" y="1" width="6" height="10" rx="1"/></svg>
          (555) 214-0799
        </li>
        <li class="contacts__item">
          <svg class="contacts__icon" viewBox="0 0 12 12" aria-hidden="true"><circle class="icon-stroke" cx="6" cy="6" r="4.8"/><path class="icon-stroke" d="M1.2 6h9.6M6 1.2c-2.4 2.8-2.4 6.8 0 9.6M6 1.2c2.4 2.8 2.4 6.8 0 9.6"/></svg>
          www.coastlinepremierretreats.example
        </li>
        <li class="contacts__item">
          <svg class="contacts__icon" viewBox="0 0 12 12" aria-hidden="true"><rect class="icon-stroke" x="1" y="3" width="10" height="7"/><path class="icon-stroke" d="M1 3l5 4 5-4"/></svg>
          info@coastlinepremierretreats.example
        </li>
      </ul>
    </div>

    <p class="tagline">Luxury Hotel &amp; Resort Email Marketing</p>

    <svg class="card__bands" viewBox="0 0 540 60" aria-hidden="true">
      <polygon class="band--white" points="232,34 540,6 540,40 250,42"/>
      <polygon class="band--orange" points="0,44 224,40 240,44 0,60"/>
    </svg>
  </section>

</main>
</body>
</html>
```